Foot doctor needs feet friendly business cards.

Business cards for Podiatrist. Needs to look professional and modern. Back side put an appointment card, and try to put a little basic street map somewhere on card along with all of our contact info below:

Marcus Dovan, DPM, Inc.
Diplomate, National Council of Lower Limb Medicine
Call: 1.877.Toes.482
1.555.283.9146
Fax: 1.555.671.3820
Email: info@DrDovanclinic.example
Web: www.DrDovanclinic.example
2847 W. Harbor Ln. Suite 204
Harborview, CA 90000

```html
<!DOCTYPE html>
<html lang="en">
<head>
<meta charset="utf-8">
<title>Marcus Dovan, DPM, Inc. – Business and Appointment Card</title>
<link rel="stylesheet" href="https://fonts.googleapis.com/css2?family=Source+Sans+3:ital,wght@0,400;0,600;1,400;1,600&display=swap">
<style>
  :root {
    --backdrop-top: #2a2a2a;
    --backdrop-bottom: #060606;
    --card-bg: #f7f7f5;
    --brand-blue: #1d4a78;
    --ink: #1a1a1a;
    --rule: #6d6d6d;
  }
  * { box-sizing: border-box; margin: 0; padding: 0; }
  html, body { width: 1200px; height: 900px; overflow: hidden; }
  body {
    position: relative;
    background: linear-gradient(180deg, var(--backdrop-top) 0%, #151515 55%, var(--backdrop-bottom) 100%);
    font-family: "Source Sans 3", "Myriad Pro", Arial, sans-serif;
    color: var(--ink);
  }
  .card {
    position: absolute;
    top: 184px;
    width: 302px;
    height: 491px;
    border-radius: 13px;
    background: var(--card-bg);
    overflow: hidden;
  }
  .card--front { left: 299px; }
  .card--back { left: 645px; width: 305px; }

  .photo-area {
    position: absolute;
    left: 0; bottom: 0;
    width: 100%;
    height: 200px;
  }
  .photo-area svg { display: block; width: 100%; height: 100%; }

  /* Front */
  .practice-name {
    position: absolute;
    top: 22px; left: 0; width: 100%;
    text-align: center;
    color: var(--brand-blue);
    font-weight: 600;
    font-size: 21px;
    letter-spacing: 0.2px;
  }
  .practice-name .suffix { font-size: 17px; }
  .credential {
    position: absolute;
    top: 52px; left: 0; width: 100%;
    text-align: center;
    font-size: 14.5px;
    line-height: 21px;
  }
  .contact-list {
    position: absolute;
    top: 124px; left: 0; width: 100%;
    list-style: none;
    font-size: 14.5px;
    line-height: 20.5px;
    text-align: center;
  }
  .contact-list li { display: flex; justify-content: center; align-items: center; gap: 3px; }
  .contact-list .icon { width: 11px; height: 11px; flex: none; }
  .contact-list .no-icon { padding-left: 14px; }
  .address {
    position: absolute;
    top: 250px; left: 0; width: 100%;
    text-align: center;
    font-size: 14.5px;
    line-height: 20.5px;
  }

  /* Back */
  .appointment-title {
    position: absolute;
    top: 36px; left: 0; width: 100%;
    text-align: center;
    color: var(--brand-blue);
    font-style: italic;
    font-weight: 600;
    font-size: 16px;
    letter-spacing: 0.3px;
  }
  .field {
    position: absolute;
    left: 25px;
    width: 242px;
    height: 18px;
    font-size: 14px;
    border-bottom: 1px solid var(--rule);
    line-height: 16px;
  }
  .field--for { top: 76px; width: 238px; }
  .field--date { top: 109px; width: 240px; }
  .field--date .time-label { position: absolute; left: 119px; }
  .field--location { top: 142px; }
  .field--blank { top: 170px; }
  .notice {
    position: absolute;
    top: 212px; left: 0; width: 100%;
    text-align: center;
    font-style: italic;
    font-weight: 600;
    font-size: 14.5px;
    line-height: 22px;
  }
</style>
</head>
<body>

  <section class="card card--front" aria-label="Business card front">
    <h1 class="practice-name">MARCUS DOVAN<span class="suffix">, DPM, INC.</span></h1>
    <p class="credential">Diplomate, National Council of<br>Lower Limb Medicine</p>

    <ul class="contact-list">
      <li>
        <svg class="icon" viewBox="0 0 12 12" aria-hidden="true"><path fill="#1d4a78" d="M1 4c0-2 2-3 5-3s5 1 5 3l-2 1-1-2H4L3 5zM3 6h6l1 5H2z"/></svg>
        <span>1.877.Toes.482</span>
      </li>
      <li class="no-icon"><span>1.555.283.9146</span></li>
      <li>
        <svg class="icon" viewBox="0 0 12 12" aria-hidden="true"><path fill="#1d4a78" d="M3 1h5v3H3zM1 4h10v7H1z"/><path fill="#f7f7f5" d="M3 6h2v1H3zM3 8h2v1H3zM7 6h2v3H7z"/></svg>
        <span>1.555.671.3820</span>
      </li>
      <li>
        <svg class="icon" viewBox="0 0 12 12" aria-hidden="true"><rect x="1" y="3" width="10" height="7" fill="#1d4a78"/><path d="M1.5 3.5l4.5 3.5 4.5-3.5" fill="none" stroke="#f7f7f5" stroke-width="0.9"/></svg>
        <span>info@DrDovanclinic.example</span>
      </li>
      <li>
        <svg class="icon" viewBox="0 0 12 12" aria-hidden="true"><path d="M5 7l2-2M4 6L2 8a1.4 1.4 0 0 0 2 2l2-2M8 6l2-2a1.4 1.4 0 0 0-2-2L6 4" fill="none" stroke="#1d4a78" stroke-width="1.3" stroke-linecap="round"/></svg>
        <span>www.DrDovanclinic.example</span>
      </li>
    </ul>

    <p class="address">2847 W. Harbor Ln. Suite 204<br>Harborview, CA 90000</p>

    <div class="photo-area" role="img" aria-label="Photo of a baby's foot cradled in an adult's hands">
      <svg viewBox="0 0 302 200" preserveAspectRatio="none" aria-hidden="true">
        <defs>
          <linearGradient id="skin-front" x1="0" y1="0" x2="0" y2="1">
            <stop offset="0" stop-color="#f7f7f5"/>
            <stop offset="0.2" stop-color="#f2d3c2"/>
            <stop offset="0.65" stop-color="#e7b49b"/>
            <stop offset="1" stop-color="#d99a80"/>
          </linearGradient>
        </defs>
        <rect width="302" height="200" fill="url(#skin-front)"/>
      </svg>
    </div>
  </section>

  <section class="card card--back" aria-label="Appointment card back">
    <h2 class="appointment-title">APPOINTMENT</h2>
    <div class="field field--for">For :</div>
    <div class="field field--date">Date :<span class="time-label">Time :</span></div>
    <div class="field field--location">Location :</div>
    <div class="field field--blank"></div>
    <p class="notice">If you&nbsp; are unable to keep appointment,<br>please contact<br>us as soon as possible. Call&nbsp; 877 555 0148</p>

    <div class="photo-area" role="img" aria-label="Photo of a baby's foot cradled in an adult's hands">
      <svg viewBox="0 0 305 200" preserveAspectRatio="none" aria-hidden="true">
        <defs>
          <linearGradient id="skin-back" x1="0" y1="0" x2="0" y2="1">
            <stop offset="0" stop-color="#f7f7f5"/>
            <stop offset="0.2" stop-color="#f2d3c2"/>
            <stop offset="0.65" stop-color="#e7b49b"/>
            <stop offset="1" stop-color="#d99a80"/>
          </linearGradient>
        </defs>
        <rect width="305" height="200" fill="url(#skin-back)"/>
      </svg>
    </div>
  </section>

</body>
</html>
```